Harborline Auto LLC

Car Dealer Customer Service
Address: 2874 Cresthaven Road, Linden Falls, NV 89999
web: www.harborlineautoxq.net
email: harborlineautoxq@mailnest.example
Phone: (555) 555-0148
Phone: (555) 555-0173

```html
<!DOCTYPE html>
<html lang="en">
<head>
<meta charset="utf-8">
<title>Harborline Auto – Business Card</title>
<link rel="stylesheet" href="https://fonts.googleapis.com/css2?family=Montserrat:wght@700;800&family=Open+Sans:wght@400&family=Oswald:wght@500&display=swap">
<style>
  :root {
    --stage: #1f1f1f;
    --brand-blue: #2587bf;
    --deep-blue: #0b3a9c;
    --brand-orange: #e9841f;
    --brand-gold: #e6a83a;
    --ink: #3a3a3a;
    --paper: #f6f6f8;
    --white: #ffffff;
  }
  * { margin: 0; padding: 0; box-sizing: border-box; }
  html, body { width: 1200px; height: 800px; overflow: hidden; background: var(--stage); }
  .canvas { position: relative; width: 1200px; height: 800px; }

  .card {
    position: absolute;
    top: 246px;
    width: 540px;
    height: 308px;
    overflow: hidden;
  }

  /* Front */
  .card--front { left: 40px; background: var(--brand-blue); }
  .front-emblem-area {
    position: absolute; left: 0; bottom: 0; width: 300px; height: 210px;
    background: linear-gradient(160deg, var(--deep-blue) 0%, #1b5fc8 40%, var(--brand-gold) 62%, var(--brand-orange) 100%);
    border-top-right-radius: 140px;
  }
  .front-wordmark {
    position: absolute; right: 36px; top: 52px;
  }
  .front-name {
    font-family: "Montserrat", sans-serif; font-weight: 800;
    font-size: 32px; color: var(--white); letter-spacing: 0.5px; line-height: 1;
    white-space: nowrap;
  }
  .front-url {
    font-family: "Montserrat", sans-serif; font-weight: 700;
    font-size: 11px; color: var(--white); letter-spacing: 2.4px; margin-top: 7px;
    white-space: nowrap;
  }

  /* Back */
  .card--back { left: 620px; background: var(--paper); }
  .back-watermark-area {
    position: absolute; right: 0; top: 40px; width: 300px; height: 232px;
    background: linear-gradient(140deg, #e3ebf3 0%, #f3ebdf 60%, #e6eef5 100%);
    border-top-left-radius: 150px;
  }
  .back-band {
    position: absolute; left: 0; bottom: 0; height: 10px; width: 100%;
    background: linear-gradient(90deg, var(--brand-blue) 0 55%, var(--brand-gold) 55% 100%);
  }
  .back-band-accent {
    position: absolute; right: 0; bottom: 10px; width: 245px; height: 14px;
    background: var(--brand-gold); opacity: 0.75;
  }
  .back-logo {
    position: absolute; left: 34px; top: 52px;
    display: flex; align-items: center; gap: 12px;
  }
  .logo-dot { width: 34px; height: 34px; border-radius: 50%; background: var(--brand-blue); flex: none; }
  .logo-name {
    font-family: "Montserrat", sans-serif; font-weight: 800;
    font-size: 26px; color: var(--brand-blue); line-height: 1; white-space: nowrap;
  }
  .contact-block {
    position: absolute; left: 34px; top: 116px;
    font-family: "Open Sans", sans-serif; font-size: 11.5px; color: var(--ink); line-height: 1.45;
  }
  .contact-list { list-style: none; margin-top: 10px; }
  .contact-list li { display: flex; align-items: center; gap: 8px; white-space: nowrap; }
  .contact-list svg { width: 11px; height: 11px; fill: var(--brand-gold); flex: none; }
  .person {
    position: absolute; right: 40px; top: 150px; text-align: right;
  }
  .person-name {
    font-family: "Oswald", sans-serif; font-weight: 500; font-size: 24px;
    color: var(--brand-blue); letter-spacing: 0.5px; line-height: 1.05; white-space: nowrap;
  }
  .person-role {
    font-family: "Open Sans", sans-serif; font-size: 12px; color: var(--brand-gold);
  }
</style>
</head>
<body>
<main class="canvas">

  <section class="card card--front" aria-label="Card front">
    <div class="front-emblem-area" role="img" aria-label="Brand emblem decoration: car over a gear in orange and blue"></div>
    <div class="front-wordmark">
      <div class="front-name">HARBORLINE AUTO</div>
      <div class="front-url">www.harborlineautoxq.net</div>
    </div>
  </section>

  <section class="card card--back" aria-label="Card back">
    <div class="back-watermark-area" role="img" aria-label="Faint brand emblem watermark in pale blue and beige"></div>
    <div class="back-band-accent"></div>
    <div class="back-band"></div>

    <div class="back-logo">
      <span class="logo-dot"></span>
      <span class="logo-name">HARBORLINE AUTO</span>
    </div>

    <div class="contact-block">
      <p>Car Dealer Customer Service</p>
      <p>2874 Cresthaven Road</p>
      <p>Linden Falls, NV 89999</p>
      <ul class="contact-list">
        <li><svg viewBox="0 0 24 24"><path d="M6.6 10.8a15.1 15.1 0 0 0 6.6 6.6l2.2-2.2c.3-.3.7-.4 1-.2 1.1.4 2.3.6 3.6.6.6 0 1 .4 1 1V20c0 .6-.4 1-1 1A17 17 0 0 1 3 4c0-.6.4-1 1-1h3.5c.6 0 1 .4 1 1 0 1.3.2 2.5.6 3.6.1.3 0 .7-.2 1z"/></svg>(555) 555-0148</li>
        <li><svg viewBox="0 0 24 24"><path d="M6.6 10.8a15.1 15.1 0 0 0 6.6 6.6l2.2-2.2c.3-.3.7-.4 1-.2 1.1.4 2.3.6 3.6.6.6 0 1 .4 1 1V20c0 .6-.4 1-1 1A17 17 0 0 1 3 4c0-.6.4-1 1-1h3.5c.6 0 1 .4 1 1 0 1.3.2 2.5.6 3.6.1.3 0 .7-.2 1z"/></svg>(555) 555-0173</li>
        <li><svg viewBox="0 0 24 24"><path d="M2 5h20v14H2zm2 2v.5l8 5 8-5V7l-8 5z"/></svg>harborlineautoxq@mailnest.example</li>
        <li><svg viewBox="0 0 24 24"><circle cx="12" cy="12" r="10"/></svg>www.harborlineautoxq.net</li>
      </ul>
    </div>

    <div class="person">
      <div class="person-name">DALTON MERCER</div>
      <div class="person-role">Founder &amp; CEO</div>
    </div>
  </section>

</main>
</body>
</html>
```